Copper lark buildworks

Copper lark buildworks is a small construction company.
Who is a licenced builder, Carpenter, joiner,
working on heritage ,new build, speacial projects and sometimes furniture

Industry/Entity Type

Construction

```html
<!DOCTYPE html>
<html lang="en">
<head>
<meta charset="utf-8">
<title>Copper lark buildworks — Business Card</title>
<link href="https://fonts.googleapis.com/css2?family=Roboto+Slab:wght@400&family=PT+Sans:wght@400;700&display=swap" rel="stylesheet">
<style>
  :root {
    --backdrop: #5f5f5f;
    --card-light: #ececec;
    --card-dark: #303030;
    --brand-green: #1ea81e;
    --ink: #2e2e2e;
    --ink-soft: #3a3a3a;
    --wordmark-light: #e2e2e2;
    --rule: #3a3a3a;
  }
  * { margin: 0; padding: 0; box-sizing: border-box; }
  html, body {
    width: 1200px;
    height: 900px;
    overflow: hidden;
    background: var(--backdrop);
  }
  .canvas {
    position: relative;
    width: 1200px;
    height: 900px;
  }
  .card {
    position: absolute;
    top: 170px;
    width: 347px;
    height: 561px;
    box-shadow: 2px 3px 6px rgba(0, 0, 0, 0.35);
  }
  .card--front { left: 259px; background: var(--card-light); }
  .card--back  { left: 632px; background: var(--card-dark); }

  .brand-dot {
    position: absolute;
    left: 50%;
    width: 92px;
    height: 92px;
    margin-left: -46px;
    border-radius: 50%;
    background: var(--brand-green);
  }
  .card--front .brand-dot { top: 92px; }
  .card--back  .brand-dot { top: 206px; }

  .wordmark {
    position: absolute;
    left: 0;
    width: 100%;
    text-align: center;
    font-family: "Roboto Slab", serif;
    font-weight: 400;
    font-size: 24px;
    line-height: 32px;
    white-space: nowrap;
  }
  .card--front .wordmark { top: 216px; color: var(--ink); }
  .card--back  .wordmark { top: 328px; color: var(--wordmark-light); }

  .contact {
    position: absolute;
    top: 319px;
    left: 0;
    width: 100%;
    text-align: center;
    font-family: "PT Sans", sans-serif;
    color: var(--ink-soft);
  }
  .contact__name {
    font-family: "Roboto Slab", serif;
    font-size: 24px;
    line-height: 32px;
    color: var(--ink);
  }
  .contact__name .first { color: var(--brand-green); }
  .contact__role {
    font-size: 15px;
    line-height: 18px;
  }
  .contact__rule {
    width: 163px;
    height: 1px;
    margin: 8px auto 9px;
    background: var(--rule);
  }
  .contact__line {
    font-size: 15px;
    line-height: 20px;
  }
  .contact__line .label {
    font-weight: 700;
    color: var(--brand-green);
  }
  .contact__web {
    font-size: 15px;
    line-height: 20px;
    font-weight: 700;
    color: var(--ink);
  }
  .contact__web .accent { color: var(--brand-green); }
  .contact__address {
    font-size: 15px;
    line-height: 20px;
  }
</style>
</head>
<body>
<main class="canvas">
  <section class="card card--front" aria-label="Card front">
    <div class="brand-dot" aria-hidden="true"></div>
    <p class="wordmark">Copper lark buildworks</p>

    <div class="contact">
      <p class="contact__name"><span class="first">Marcus</span> Hale</p>
      <p class="contact__role">Managing Director</p>
      <div class="contact__rule"></div>
      <p class="contact__line"><span class="label">P:</span> 044-123 456 789</p>
      <p class="contact__line"><span class="label">M:</span> 044-123 456 789</p>
      <p class="contact__line"><span class="label">E:</span> info@copperlark.com</p>
      <p class="contact__web"><span class="accent">www.</span>copperlarkbuild<span class="accent">.com</span></p>
      <div class="contact__rule"></div>
      <p class="contact__address">12345, Address Goes Here</p>
      <p class="contact__address">Country Name, 123456.</p>
    </div>
  </section>

  <section class="card card--back" aria-label="Card back">
    <div class="brand-dot" aria-hidden="true"></div>
    <p class="wordmark">Copper lark buildworks</p>
  </section>
</main>
</body>
</html>
```